Modern looking signage for dental office.

Exterior signage for passing cars
Updates
Need extra days to review
Target Market(s)
Cars passing by
Font styles to use
Sans Serif
Colors
3276b5
Requirements
Must have
- Logo
- OPEN ON SUTURDAY AND SUNDAY
- NIGHT CLINIC AVAILABLE
- PLEASE USE THE FONT TYPE IN FILE 4 UPLOADED BELOW.
- (847) 302-7469
- Modern looking

```html
<!DOCTYPE html>
<html lang="en">
<head>
<meta charset="utf-8">
<title>Halden Dental – Weekend &amp; Night Clinic Sign</title>
<link href="https://fonts.googleapis.com/css2?family=Montserrat:wght@400;500;700;800&display=swap" rel="stylesheet">
<style>
  :root {
    --backdrop: #8c8c8c;
    --sign-white: #ffffff;
    --band-black: #0b0b0b;
    --soft-grey: #d9d9d9;
    --highlight-grey: #bdbdbd;
    --ink-dark: #3b3b3d;
    --ink-black: #111111;
    --rule-grey: #9a9a9a;
    --accent-blue: #3276b5;
  }
  * { margin: 0; padding: 0; box-sizing: border-box; }
  html, body {
    width: 1200px; height: 1000px; overflow: hidden;
    background: var(--backdrop);
    font-family: "Montserrat", sans-serif;
  }
  .sign {
    position: absolute; left: 193px; top: 92px;
    width: 814px; height: 813px;
    background: var(--sign-white);
    overflow: hidden;
  }
  .sign-shapes { position: absolute; inset: 0; }
  .brand {
    position: absolute; left: 66px; top: 46px;
    display: flex; align-items: center; gap: 26px;
  }
  .brand-circle {
    width: 144px; height: 144px; border-radius: 50%;
    border: 3px solid var(--ink-dark);
  }
  .brand-name {
    font-weight: 400; font-size: 66px; letter-spacing: 1px;
    color: var(--ink-dark); line-height: 1;
  }
  .tagline {
    position: absolute; left: 236px; top: 175px;
    font-weight: 500; font-size: 26px; color: var(--ink-dark);
    letter-spacing: 0.3px; white-space: nowrap;
  }
  .hours {
    position: absolute; left: 0; width: 100%; top: 318px;
    text-align: center; color: var(--sign-white);
  }
  .hours-open { font-weight: 800; font-size: 82px; line-height: 1; }
  .hours-days { font-weight: 800; font-size: 50px; line-height: 1; margin-top: 14px; color: #ececec; }
  .hours-rule {
    width: 364px; height: 3px; background: var(--rule-grey);
    margin: 28px auto 32px;
  }
  .hours-night { font-weight: 500; font-size: 46px; line-height: 1; }
  .hours-times { font-weight: 700; font-size: 48px; line-height: 1; margin-top: 10px; }
  .contact {
    position: absolute; left: 104px; top: 718px;
    display: flex; align-items: center; gap: 22px;
  }
  .contact-icon { width: 66px; height: 66px; }
  .contact-number {
    font-weight: 800; font-size: 80px; line-height: 1;
    color: var(--ink-black); white-space: nowrap;
  }
</style>
</head>
<body>
  <div class="sign">
    <svg class="sign-shapes" width="814" height="813" viewBox="0 0 814 813" aria-hidden="true">
      <path d="M0,180 Q430,205 814,262 L814,813 L0,813 Z" fill="var(--highlight-grey)"/>
      <path d="M0,198 Q430,208 814,258 L814,813 L0,813 Z" fill="var(--band-black)"/>
      <path d="M0,665 Q430,620 814,668 L814,813 L0,813 Z" fill="var(--highlight-grey)"/>
      <path d="M0,680 Q430,640 814,688 L814,813 L0,813 Z" fill="var(--soft-grey)"/>
      <rect y="760" width="814" height="53" fill="#e6e6e6" opacity="0.6"/>
    </svg>

    <div class="brand">
      <div class="brand-circle"></div>
      <div class="brand-name">HALDEN DENTAL</div>
    </div>
    <div class="tagline">MODERN GENERAL DENTISTRY</div>

    <div class="hours">
      <div class="hours-open">OPEN ON</div>
      <div class="hours-days">SATURDAY AND SUNDAY</div>
      <div class="hours-rule"></div>
      <div class="hours-night">NIGHT CLINIC FROM</div>
      <div class="hours-times">5PM TO 10PM AVAILABLE</div>
    </div>

    <div class="contact">
      <svg class="contact-icon" viewBox="0 0 66 66" aria-hidden="true">
        <circle cx="33" cy="33" r="31" fill="#8a8a8a"/>
        <circle cx="33" cy="33" r="25" fill="var(--sign-white)"/>
        <path d="M22,20 l6,-2 l4,8 l-4,3 q3,7 9,10 l3,-4 l8,4 l-2,6 q-4,3 -10,0 q-11,-6 -16,-17 q-2,-5 2,-8 Z" fill="var(--ink-black)"/>
        <path d="M37,20 q8,1 9,9 M37,15 q13,1 14,14" stroke="var(--ink-black)" stroke-width="2.5" fill="none" stroke-linecap="round"/>
      </svg>
      <div class="contact-number">847 302 7469</div>
    </div>
  </div>
</body>
</html>
```